Pet sitting Business needs a website

We need a website that shows our services and prices. Shows our love of animals but also our professionalism. want a gallery, about, blog, services, links to fb and instagram accounts, newsletter archive. want it to be easy to access and wonderful to navigate. want the domain to be Birchfordpawhaven.com
take any info from FB site www.facebook.com/birchfordpawhaven
I would like it to fit square space platform

Target Market(s)

upscale area, responsible pet owners,

Industry/Entity Type

Pet Care

Coding

Coded - Design and coding required

Number of Pages Required

5+ page

Font styles to use
Sans Serif

Requirements
Must have
• (square space platform)
• Menu
• photo gallery
• about us
• services
• policies
• monthly newsletter
• unavailable dates
• Introduction (welcome)
• payment methods
• Daily updates
• testimonials (use from fb site)
Should not have
• stock photos

```html
<!DOCTYPE html>
<html lang="en">
<head>
<meta charset="utf-8">
<title>Birchford Paw Haven Pet Club</title>
<link href="https://fonts.googleapis.com/css2?family=Oswald:wght@400;500&family=Open+Sans:wght@400;600;700&display=swap" rel="stylesheet">
<style>
:root{
  --blue:#1c8fc9;
  --blue-dark:#1579ad;
  --gold:#e3a21a;
  --ink:#333;
  --muted:#8a8a8a;
  --light:#f0f0f0;
  --footer:#2a2a2a;
  --footer-deep:#1f1f1f;
  --white:#fff;
}
*{box-sizing:border-box;margin:0;padding:0}
html,body{width:1200px;height:3228px;overflow:hidden}
body{font-family:"Open Sans",Arial,sans-serif;color:var(--ink);background:var(--white);font-size:13px;line-height:1.6}
.heading{font-family:"Oswald",Arial,sans-serif;font-weight:400}
.heading .accent{color:var(--blue)}
.btn{display:inline-block;background:var(--blue);color:var(--white);font-size:11px;font-weight:700;text-transform:uppercase;padding:9px 18px;letter-spacing:.5px}

/* header */
.site-header{height:120px;display:flex;justify-content:space-between;align-items:center;padding:0 60px}
.brand{display:flex;align-items:center;gap:14px}
.brand-dot{width:52px;height:52px;border-radius:50%;background:var(--gold)}
.brand-name{font-family:"Open Sans",sans-serif;font-weight:700;color:var(--gold);font-size:18px;line-height:1.2;width:170px}
.header-info{text-align:right}
.header-contact{font-size:12px;color:var(--muted)}
.header-social{display:flex;gap:8px;justify-content:flex-end;margin-top:12px}
.header-social span{width:22px;height:22px;background:var(--gold);display:block}

/* nav */
.main-nav{height:36px;background:var(--blue);display:flex;justify-content:center;gap:0}
.main-nav a{color:var(--white);text-decoration:none;font-size:12px;font-weight:600;padding:0 22px;line-height:36px}
.main-nav a.active{background:var(--gold)}

/* hero */
.hero{height:444px;position:relative;background:linear-gradient(180deg,#7a8a8f 0%,#a59060 45%,#8d6a35 100%)}
.hero-title{position:absolute;left:0;right:0;bottom:24px;text-align:center;color:var(--white);font-size:44px;font-family:"Oswald",sans-serif;font-weight:500}

/* welcome */
.welcome{height:300px;text-align:center;padding-top:40px}
.welcome h2{font-size:32px;margin-bottom:18px}
.welcome p{width:860px;margin:0 auto 22px;color:var(--muted);font-size:12px}

/* gallery */
.gallery{height:810px;background:var(--light);padding-top:38px}
.gallery h2{text-align:center;font-size:32px;margin-bottom:34px}
.gallery-grid{width:1000px;margin:0 auto;display:grid;grid-template-columns:repeat(4,1fr);gap:20px}
.gallery-grid div{height:300px}
.g1{background:linear-gradient(135deg,#d8c6a6,#b7946a)}
.g2{background:linear-gradient(135deg,#7c8a4e,#c59a6b)}
.g3{background:linear-gradient(135deg,#c3d48a,#eadfc9)}
.g4{background:linear-gradient(135deg,#7f9a4d,#c9a267)}
.g5{background:linear-gradient(135deg,#5e8d3c,#d9b58c)}
.g6{background:linear-gradient(135deg,#9ab3c9,#e8e2d4)}
.g7{background:linear-gradient(135deg,#8c8a80,#c8b39c)}
.g8{background:linear-gradient(135deg,#b59b7a,#4e4a44)}

/* about */
.about{height:360px;display:flex;gap:60px;padding:40px 100px 0}
.about-text{flex:1}
.about h2{font-size:30px;margin-bottom:10px}
.about h3{font-size:14px;font-weight:700;margin-bottom:12px}
.about p{color:var(--muted);font-size:12px;margin-bottom:14px}
.about-photo{width:460px;height:250px;background:linear-gradient(135deg,#f0ece6,#d9a74f)}

/* newsletter */
.newsletter{height:170px;background:var(--gold);padding:24px 100px 0;color:var(--white)}
.newsletter h2{font-size:26px}
.newsletter p{font-size:11px;margin-bottom:18px}
.newsletter-form{display:flex;gap:14px}
.newsletter-form span{height:40px;background:var(--white);color:var(--muted);font-size:12px;padding:0 14px;line-height:40px;width:230px}
.newsletter-form .subscribe{background:#222;color:var(--white);font-weight:700;width:120px;text-align:center;font-size:11px}

/* news */
.news{height:590px;padding-top:40px}
.news h2{text-align:center;font-size:32px;margin-bottom:34px}
.news-grid{width:1000px;margin:0 auto;display:grid;grid-template-columns:repeat(3,1fr);gap:30px}
.news-img{height:230px;margin-bottom:16px}
.n1{background:linear-gradient(135deg,#e3ded4,#9b6a3e)}
.n2{background:linear-gradient(135deg,#9db3c5,#7c6a52)}
.n3{background:linear-gradient(135deg,#e7e4e0,#b9b6ae)}
.news-card h3{font-size:15px;font-weight:700;margin-bottom:2px}
.news-date{color:var(--gold);font-size:11px;font-weight:600}
.news-card p{color:var(--muted);font-size:12px;margin:8px 0}
.read-more{color:var(--gold);font-size:11px;font-weight:700;text-transform:uppercase}

/* testimonial */
.testimonial{height:190px;background:var(--blue);color:var(--white);padding-top:24px}
.testimonial h2{text-align:center;font-size:28px;margin-bottom:22px}
.quotes{width:1000px;margin:0 auto;display:grid;grid-template-columns:1fr 1fr;gap:60px}
.quote{display:flex;gap:18px}
.avatar{width:70px;height:70px;border-radius:50%;background:linear-gradient(135deg,#e8d6c4,#a9836a);flex:none}
.quote p{font-size:11px;line-height:1.55}
.quote strong{display:block;font-size:11px;margin-top:4px;text-transform:uppercase}

/* footer */
.site-footer{height:170px;background:var(--footer);color:#bbb;display:grid;grid-template-columns:repeat(4,1fr);gap:40px;padding:22px 100px 0;font-size:11px}
.site-footer h4{color:var(--white);font-size:13px;font-weight:700;text-transform:uppercase;margin-bottom:10px}
.tweet{display:flex;gap:6px;margin-bottom:6px}
.tweet svg{flex:none;margin-top:3px}
.footer-form{display:flex;margin-top:8px}
.footer-form span{background:var(--white);color:var(--muted);height:28px;line-height:28px;padding:0 8px;width:150px}
.footer-form .signup{background:var(--gold);color:var(--white);width:60px;text-align:center;font-weight:700}
.footer-social{display:flex;gap:8px}
.footer-social span{width:28px;height:28px;background:var(--blue);display:block}
.bottom-bar{height:38px;background:var(--footer-deep);color:#888;font-size:11px;display:flex;justify-content:center;align-items:center}
</style>
</head>
<body>

<header class="site-header">
  <div class="brand">
    <span class="brand-dot"></span>
    <span class="brand-name">Birchford Paw Haven</span>
  </div>
  <div class="header-info">
    <div class="header-contact">Tel.: (+800) 514-2290 &nbsp;|&nbsp; info@birchfordpawhaven.com</div>
    <div class="header-social" aria-label="Social links">
      <span></span><span></span><span></span><span></span>
    </div>
  </div>
</header>

<nav class="main-nav">
  <a class="active">Home</a><a>Photo gallery</a><a>About us</a><a>Services</a><a>Policies</a><a>Monthly newsletter</a><a>Unavailable dates</a><a>Introduction</a><a>Payment methods</a>
</nav>

<section class="hero" role="img" aria-label="Child in a striped shirt hugging a golden dog in a wheat field">
  <h1 class="hero-title">Birchford Paw Haven Pet Sitting Club</h1>
</section>

<section class="welcome">
  <h2 class="heading">Welcome to <span class="accent">Birchford Paw Haven Pet Club</span></h2>
  <p>We care for your pets as if they were our own. Our sitters visit your home, keep familiar routines, send daily updates and photos, and treat every dog, cat and small friend with patience, kindness and proven professional care. Book a visit and let your companion stay happy, safe and relaxed in the comfort of home while you are away.</p>
  <span class="btn">Learn more</span>
</section>

<section class="gallery">
  <h2 class="heading">Our Photogallery</h2>
  <div class="gallery-grid">
    <div class="g1" role="img" aria-label="Puppy and kitten together"></div>
    <div class="g2" role="img" aria-label="Woman holding a small dog"></div>
    <div class="g3" role="img" aria-label="White puppy on grass"></div>
    <div class="g4" role="img" aria-label="Dog lying in the garden"></div>
    <div class="g5" role="img" aria-label="Boy hugging a dog outdoors"></div>
    <div class="g6" role="img" aria-label="Small dog with a toy"></div>
    <div class="g7" role="img" aria-label="Cat resting indoors"></div>
    <div class="g8" role="img" aria-label="French bulldog portrait"></div>
  </div>
</section>

<section class="about">
  <div class="about-text">
    <h2 class="heading">About <span class="accent">us</span></h2>
    <h3>Where kisses and hugs are my speciality</h3>
    <p>Birchford Paw Haven began with one simple idea: pets are family. For over ten years we have cared for dogs, cats and small pets across the neighbourhood, offering home visits, walks and overnight stays with calm, reliable and loving attention.</p>
    <p>Every sitter is insured, trained in pet first aid and matched to your pet's needs, so you can travel with full peace of mind.</p>
    <span class="btn">Learn more</span>
  </div>
  <div class="about-photo" role="img" aria-label="Woman smiling with a golden retriever"></div>
</section>

<section class="newsletter">
  <h2 class="heading">Our Newsletter</h2>
  <p>Subscribe to our monthly newsletter for pet care tips, club news, holiday booking reminders and updates on our unavailable dates.</p>
  <div class="newsletter-form">
    <span>Your name</span><span>Your email</span><span>Your phone</span><span class="subscribe">SUBSCRIBE</span>
  </div>
</section>

<section class="news">
  <h2 class="heading">Club <span class="accent">News</span></h2>
  <div class="news-grid">
    <article class="news-card">
      <div class="news-img n1" role="img" aria-label="Puppy sitting on a wooden floor"></div>
      <h3>Now There's A Company That Will Make</h3>
      <div class="news-date">July 21, 2016</div>
      <p>Our sitters share simple routines that help your dog feel settled and calm while you are away for the weekend.</p>
      <span class="read-more">Read more »</span>
    </article>
    <article class="news-card">
      <div class="news-img n2" role="img" aria-label="Dog standing on a city path"></div>
      <h3>These prices are for customers</h3>
      <div class="news-date">July 21, 2016</div>
      <p>See our updated visit packages and discounts for regular clients, multi-pet homes and longer holiday stays.</p>
      <span class="read-more">Read more »</span>
    </article>
    <article class="news-card">
      <div class="news-img n3" role="img" aria-label="Woman at home with two dogs"></div>
      <h3>What's happened with two dogs</h3>
      <div class="news-date">July 21, 2016</div>
      <p>A happy story of two shy rescue dogs who became best friends during a two week stay with our team.</p>
      <span class="read-more">Read more »</span>
    </article>
  </div>
</section>

<section class="testimonial">
  <h2 class="heading">Testimonial</h2>
  <div class="quotes">
    <div class="quote">
      <div class="avatar" role="img" aria-label="Client portrait"></div>
      <p>“The team looked after our two cats for a month and sent photos every single day. We came home to relaxed, happy pets and a spotless house.”<strong>Dana Whitcombe</strong></p>
    </div>
    <div class="quote">
      <div class="avatar" role="img" aria-label="Client portrait"></div>
      <p>“Reliable, friendly and truly professional. Our old dog needs medicine twice a day and they never missed a dose. Highly recommended.”<strong>Marcus Ellery</strong></p>
    </div>
  </div>
</section>

<footer class="site-footer">
  <div>
    <h4>Contact us</h4>
    <p>14 Larkspur Lane, Suite 3<br>Birchford, NY 10520</p>
    <p style="margin-top:6px">(+800) 514-2290<br>info@birchfordpawhaven.com</p>
  </div>
  <div>
    <h4>Latest tweets</h4>
    <div class="tweet"><svg width="10" height="10" viewBox="0 0 10 10"><path d="M1 5l3 3 5-6" stroke="#1c8fc9" stroke-width="2" fill="none"/></svg><span>Spring walk slots now open, book early for the holidays.</span></div>
    <div class="tweet"><svg width="10" height="10" viewBox="0 0 10 10"><path d="M1 5l3 3 5-6" stroke="#1c8fc9" stroke-width="2" fill="none"/></svg><span>New photos from this week's park visits are up.</span></div>
  </div>
  <div>
    <h4>Newsletter</h4>
    <p>Get pet tips and club news in your inbox every month.</p>
    <div class="footer-form"><span>Enter your email</span><span class="signup">Sign Up</span></div>
  </div>
  <div>
    <h4>Social media</h4>
    <div class="footer-social" aria-label="Social links"><span></span><span></span><span></span></div>
  </div>
</footer>
<div class="bottom-bar">2016 © All Rights Reserved &nbsp;|&nbsp; Birchfordpawhaven.com</div>

</body>
</html>
```